Residential Remodeling Contractor needs updated business card

I need a new design for my business card.
Name of the company is Ridgefell Construction. I need a card that commands presence, strength, integrity. I have been in business for 28 years. I am a Residential Remodeling Contractor that covers all aspects of a residential remodel and build.

```html
<!DOCTYPE html>
<html lang="en">
<head>
<meta charset="utf-8">
<title>Ridgefell Construction – Business Card</title>
<link href="https://fonts.googleapis.com/css2?family=Montserrat:ital,wght@0,400;0,500;0,700;0,800;1,400&display=swap" rel="stylesheet">
<style>
  :root {
    --navy: #203b7e;
    --white: #ffffff;
    --stage: #1b1b1d;
  }
  html, body {
    margin: 0;
    width: 1200px;
    height: 963px;
    overflow: hidden;
    background: var(--stage);
    font-family: "Montserrat", sans-serif;
  }
  .canvas {
    position: relative;
    width: 1200px;
    height: 963px;
  }
  .card {
    position: absolute;
    left: 222px;
    width: 756px;
    height: 432px;
    background: var(--navy);
    border-radius: 18px;
    overflow: hidden;
    color: var(--white);
  }
  .card--front { top: 34px; }
  .card--back { top: 497px; }

  /* brand lockup */
  .brand {
    display: flex;
    align-items: center;
    gap: 14px;
    font-weight: 700;
    text-transform: uppercase;
    letter-spacing: 0.08em;
    line-height: 1.05;
    color: var(--white);
  }
  .brand__mark {
    background: var(--white);
    flex: none;
  }
  .brand__name span { display: block; }

  /* front */
  .card--front .brand {
    position: absolute;
    left: 48px;
    top: 40px;
    font-size: 26px;
  }
  .card--front .brand__mark { width: 40px; height: 40px; }
  .holder {
    position: absolute;
    left: 48px;
    top: 150px;
  }
  .holder__name {
    margin: 0;
    font-size: 30px;
    font-weight: 800;
    letter-spacing: 0.03em;
    text-transform: uppercase;
  }
  .holder__title {
    margin: 2px 0 0;
    font-size: 16px;
    font-weight: 400;
  }
  .rule {
    position: absolute;
    left: 48px;
    top: 232px;
    width: 660px;
    height: 2px;
    background: var(--white);
  }
  .contacts {
    position: absolute;
    left: 48px;
    top: 250px;
    margin: 0;
    padding: 0;
    list-style: none;
    font-size: 16px;
    line-height: 1.6;
  }
  .contacts li { display: flex; align-items: center; gap: 10px; }
  .contacts svg { width: 16px; height: 16px; flex: none; }
  .address {
    position: absolute;
    right: 48px;
    top: 250px;
    margin: 0;
    font-style: normal;
    font-size: 18px;
    line-height: 1.45;
    text-align: right;
  }
  .band {
    position: absolute;
    left: 0;
    bottom: 0;
    width: 756px;
    height: 96px;
  }
  .band__tagline {
    position: absolute;
    right: 48px;
    bottom: 12px;
    margin: 0;
    font-size: 14px;
    line-height: 1.2;
    font-style: italic;
    color: var(--navy);
  }

  /* back */
  .card--back {
    display: flex;
    flex-direction: column;
    align-items: center;
    justify-content: center;
    gap: 34px;
  }
  .card--back .brand { font-size: 40px; }
  .card--back .brand__mark { width: 58px; height: 58px; }
  .tagline {
    margin: 0;
    font-size: 19px;
    font-weight: 700;
    letter-spacing: 0.08em;
    text-transform: uppercase;
  }
</style>
</head>
<body>
<main class="canvas">

  <section class="card card--front" aria-label="Business card front">
    <div class="brand">
      <span class="brand__mark"></span>
      <span class="brand__name"><span>Ridgefell</span><span>Construction</span></span>
    </div>

    <div class="holder">
      <h1 class="holder__name">Marcus Delaney</h1>
      <p class="holder__title">Director</p>
    </div>

    <div class="rule"></div>

    <ul class="contacts">
      <li>
        <svg viewBox="0 0 16 16" aria-hidden="true"><path d="M4 1.5l2.5 3-1.6 1.6c.8 1.9 2.3 3.4 4.2 4.2l1.6-1.6 3 2.5-1.4 2.8C6.5 13.5 2.5 9.5 1.5 3z" fill="none" stroke="#fff" stroke-width="1.3" stroke-linejoin="round"/></svg>
        (555) 218-4470
      </li>
      <li>
        <svg viewBox="0 0 16 16" aria-hidden="true"><rect x="1.5" y="3.5" width="13" height="9" fill="none" stroke="#fff" stroke-width="1.3"/><path d="M1.5 3.5L8 9l6.5-5.5" fill="none" stroke="#fff" stroke-width="1.3"/></svg>
        info@ridgefellbuild.com
      </li>
      <li>
        <svg viewBox="0 0 16 16" aria-hidden="true"><circle cx="8" cy="8" r="6.5" fill="none" stroke="#fff" stroke-width="1.3"/><ellipse cx="8" cy="8" rx="3" ry="6.5" fill="none" stroke="#fff" stroke-width="1.1"/><path d="M1.5 8h13M2.5 5h11M2.5 11h11" stroke="#fff" stroke-width="1.1"/></svg>
        www.ridgefellbuild.com
      </li>
    </ul>

    <address class="address">128 Alder Street<br>Brookvale, GA 30512</address>

    <svg class="band" viewBox="0 0 756 96" preserveAspectRatio="none" aria-hidden="true">
      <path d="M0 40 L380 68 Q405 70 425 58 L756 58 L756 96 L0 96 Z" fill="#fff"/>
      <path d="M0 10 L370 46" stroke="#fff" stroke-width="5"/>
      <path d="M0 22 L380 56" stroke="#fff" stroke-width="3"/>
    </svg>
    <p class="band__tagline">I have been in business for 28 years</p>
  </section>

  <section class="card card--back" aria-label="Business card back">
    <div class="brand">
      <span class="brand__mark"></span>
      <span class="brand__name"><span>Ridgefell</span><span>Construction</span></span>
    </div>
    <p class="tagline">I have been in business for 28 years</p>
  </section>

</main>
</body>
</html>
```